Tamarind Lodgings letterhead

We need a letterhead designed that includes the new logo that has just been designed for our business. The letterhead will need to be formatted for digital use as well as for print.

Target Market(s)

Private tenant, corporate tenants, real estate agents

Industry/Entity Type

Digital

Requirements
Must have
• ABN 87 504 912 386
PO Box 7816, Harlowe Mail Centre QLD 4790
Email: linus.pardoe@quillmail.example
Ph: 0438 617 209

```html
<!DOCTYPE html>
<html lang="en">
<head>
<meta charset="utf-8">
<title>Tamarind Lodgings – Letterhead</title>
<link rel="stylesheet" href="https://fonts.googleapis.com/css2?family=Baloo+2:wght@500;700&display=swap">
<style>
  :root {
    --brand-maroon: #7b2c25;
    --brand-red: #a8302b;
    --paper: #ffffff;
  }
  html, body {
    margin: 0;
    padding: 0;
    overflow: hidden;
    background: var(--paper);
  }
  .letterhead {
    position: relative;
    width: 850px;
    height: 1200px;
    overflow: hidden;
    background: var(--paper);
    font-family: "Baloo 2", sans-serif;
  }
  .brand {
    position: absolute;
    left: 42px;
    top: 38px;
    display: flex;
    align-items: center;
    gap: 14px;
  }
  .brand-square {
    width: 52px;
    height: 52px;
    border-radius: 8px;
    background: var(--brand-maroon);
  }
  .brand-name {
    margin: 0;
    font-size: 30px;
    font-weight: 700;
    line-height: 1;
    color: var(--brand-maroon);
  }
  .contact {
    position: absolute;
    left: 507px;
    top: 34px;
    margin: 0;
    padding: 0;
    list-style: none;
    font-size: 18px;
    font-weight: 500;
    line-height: 25px;
    color: var(--brand-maroon);
  }
  .header-rule {
    position: absolute;
    left: 0;
    top: 169px;
    width: 850px;
    height: 3px;
    background: var(--brand-red);
  }
  .footer-wave {
    position: absolute;
    left: 0;
    bottom: 0;
    width: 850px;
    height: 160px;
    display: block;
  }
</style>
</head>
<body>
  <main class="letterhead">
    <header class="brand">
      <span class="brand-square"></span>
      <h1 class="brand-name">Tamarind Lodgings</h1>
    </header>

    <ul class="contact">
      <li>ABN 87 504 912 386</li>
      <li>PO BOX 7816, Harlowe Mail Centre</li>
      <li>QLD 4790</li>
      <li>EMAIL : linus.pardoe@quillmail.example</li>
      <li>PHONE : 0438 617 209</li>
    </ul>

    <div class="header-rule"></div>

    <svg class="footer-wave" viewBox="0 0 850 160" preserveAspectRatio="none" aria-hidden="true">
      <path d="M0 42 C60 28 120 14 190 14 C300 14 420 70 540 84 C650 96 760 70 850 52 L850 160 L0 160 Z" fill="var(--brand-maroon)"/>
    </svg>
  </main>
</body>
</html>
```